Email Signature and a letter head

I need a professional email signature and a letter head for letters sent by post. I've attached my logo and a signature i am currently using. Current letter head is also attached.

Target Market(s)

Accounting Clients

Industry/Entity Type

Public Accounting

Font styles to use
Sans Serif

Colors

Designer to choose colors to be used in the design.

Requirements
Must have
• My logo, RM Logo, Lumo Logo, Tax Agent logo. All attached.
• All my credentials - examples in the attached documents

```html
<!DOCTYPE html>
<html lang="en">
<head>
<meta charset="utf-8">
<title>Northvale Business Services – Letterhead and Email Signature</title>
<link href="https://fonts.googleapis.com/css2?family=Cinzel:wght@500&family=Lora:wght@400&family=Tinos&family=Open+Sans:wght@400;600&display=swap" rel="stylesheet">
<style>
:root{
  --gold:#a68a2b;
  --charcoal:#333335;
  --paper:#f8f8f8;
  --stage:#b3b3b3;
  --rule:#d9d9d9;
  --faint:#ebebeb;
  --ink:#444;
  --navy:#2b3f7a;
  --leaf:#2e8b2e;
  --teal:#1391c9;
  --teal-dark:#0e6e89;
}
*{box-sizing:border-box;margin:0;padding:0}
html,body{width:1200px;height:872px;overflow:hidden;background:var(--stage)}
.canvas{position:relative;width:1200px;height:872px}

/* ---------- Letterhead ---------- */
.letterhead{position:absolute;left:182px;top:145px;width:411px;height:581px;background:var(--paper);overflow:hidden}
.brand{position:absolute;text-align:center;color:var(--gold)}
.brand .mark{display:block;margin:0 auto;border:2px solid var(--gold);border-radius:50%}
.brand .name{font-family:"Cinzel",serif;font-weight:500;white-space:nowrap}
.brand .tag{font-family:"Open Sans",sans-serif;letter-spacing:.28em;white-space:nowrap}
.letterhead .brand{left:20px;top:30px;width:140px}
.letterhead .brand .mark{width:54px;height:54px}
.letterhead .brand .name{font-size:14px;margin-top:3px;letter-spacing:.02em}
.letterhead .brand .tag{font-size:5.5px;margin-top:1px}
.principal{position:absolute;right:27px;top:72px;text-align:right;color:var(--gold)}
.principal .person{font-family:"Lora",serif;font-size:12.5px}
.principal .ids{font-family:"Tinos",serif;font-size:7px;margin-top:3px;color:var(--gold)}
.principal .ids b{font-weight:400;color:var(--ink)}
.header-rule{position:absolute;left:147px;top:107px;width:236px;height:1px;background:var(--gold)}
.watermark{position:absolute;left:60px;top:149px;width:292px;height:292px;border:5px solid var(--faint);border-radius:50%;display:flex;align-items:center;justify-content:center;font-family:"Cinzel",serif;font-size:54px;color:var(--faint)}
.partners{position:absolute;left:28px;top:500px;display:flex;align-items:center;gap:10px}
.partner-lumo{display:flex;align-items:center;gap:3px}
.partner-lumo .dot{width:24px;height:24px;border-radius:50%;background:var(--teal)}
.partner-lumo .label{font-family:"Open Sans",sans-serif;font-size:8px;color:var(--teal-dark);font-weight:600}
.partner-rm{font-family:"Open Sans",sans-serif;font-size:11px;font-weight:600;color:#c8332d}
.partner-tax{display:flex;align-items:center;gap:3px;font-family:"Open Sans",sans-serif;font-size:5px;line-height:1.2;color:#222;font-weight:600}
.partner-tax .seal{width:24px;height:24px;border-radius:50%;background:#cde03a;border:2px solid #ddd}
.wave{position:absolute;left:0;bottom:0}
.contact{position:absolute;text-align:right;font-family:"Tinos",serif;color:#fff;white-space:nowrap}
.contact li{list-style:none;display:flex;justify-content:flex-end;align-items:center;gap:3px}
.contact svg{fill:#fff}
.letterhead .contact{right:18px;top:670px;top:535px;font-size:7.4px;line-height:8.6px}

/* ---------- Email window ---------- */
.email{position:absolute;left:618px;top:265px;width:398px;height:341px;background:var(--paper);font-family:"Open Sans",sans-serif;color:var(--ink);overflow:hidden}
.toolbar{position:absolute;left:9px;top:7px;display:flex;gap:14px;font-size:8px;align-items:center}
.toolbar span{display:flex;align-items:center;gap:3px}
.field-btn{position:absolute;left:14px;width:34px;height:16px;border:1px solid var(--rule);background:#fff;font-size:6.5px;font-weight:600;display:flex;align-items:center;justify-content:center}
.field-rule{position:absolute;left:7px;width:384px;height:1px;background:var(--rule)}
.bcc{position:absolute;right:12px;top:41px;font-size:6.5px;color:#777}
.subject{position:absolute;left:14px;top:102px;font-size:6.8px;color:#666}
.body-frame{position:absolute;left:7px;top:122px;width:384px;height:240px;border:1px solid var(--rule)}
.email .brand{left:34px;top:143px;width:132px}
.email .brand .mark{width:49px;height:49px}
.email .brand .name{font-size:12.5px;margin-top:2px}
.email .brand .tag{font-size:5px}
.email .wave{left:14px;top:171px;bottom:auto}
.email .contact{right:38px;top:209px;font-size:6.2px;line-height:8px}
.disclaimer{position:absolute;left:17px;top:253px;width:370px;font-size:5.2px;line-height:7.4px;color:var(--navy)}
.eco{position:absolute;left:26px;top:279px;display:flex;align-items:center;gap:11px;font-size:5.4px;color:var(--leaf)}
</style>
</head>
<body>
<div class="canvas">

  <section class="letterhead">
    <div class="brand">
      <span class="mark"></span>
      <div class="name">Northvale</div>
      <div class="tag">BUSINESS SERVICES</div>
    </div>

    <div class="principal">
      <div class="person">Marla Quinn RM BBus.</div>
      <div class="ids">ABN: <b>51 302 447 916</b> &nbsp;|&nbsp; TAN: <b>318 704 26</b></div>
    </div>
    <div class="header-rule"></div>

    <div class="watermark">Northvale</div>

    <div class="partners">
      <div class="partner-lumo"><span class="dot"></span><span class="label">Lumo</span></div>
      <div class="partner-rm">RM</div>
      <div class="partner-tax"><span class="seal"></span><span>Tax Agent<br>31870426</span></div>
    </div>

    <svg class="wave" width="411" height="112" viewBox="0 600 514 127" aria-hidden="true">
      <path d="M0,700 C120,735 250,700 340,660 S460,622 514,622 L514,727 L0,727Z" fill="var(--gold)"/>
      <path d="M0,655 C60,698 170,712 260,688 C340,664 420,614 514,609 L514,620 C420,626 345,676 262,702 C165,730 60,722 0,690Z" fill="var(--charcoal)"/>
      <path d="M30,690 C120,722 200,712 270,694" stroke="var(--charcoal)" stroke-width="2" fill="none"/>
    </svg>

    <ul class="contact">
      <li>0412555019 <svg width="6" height="6" viewBox="0 0 10 10"><path d="M2 1h2l1 2-1.3 1a6 6 0 0 0 2.3 2.3L7 5l2 1v2a1 1 0 0 1-1 1A8 8 0 0 1 1 2a1 1 0 0 1 1-1z"/></svg></li>
      <li>www.northvalebusinessservices.com.au <svg width="6" height="6" viewBox="0 0 10 10"><circle cx="5" cy="5" r="4"/></svg></li>
      <li>marla@northvalebusinessservices.com.au <svg width="6" height="6" viewBox="0 0 10 10"><rect x="1" y="2" width="8" height="6"/></svg></li>
      <li>18 Ridgeway Crescent Elmhurst VIC 3921 <svg width="6" height="6" viewBox="0 0 10 10"><path d="M5 0a3.5 3.5 0 0 1 3.5 3.5C8.5 6 5 10 5 10S1.5 6 1.5 3.5A3.5 3.5 0 0 1 5 0z"/></svg></li>
    </ul>
  </section>

  <section class="email">
    <div class="toolbar">
      <span><svg width="10" height="8" viewBox="0 0 10 8"><rect x=".5" y=".5" width="9" height="7" fill="none" stroke="#2b5fa8"/><path d="M.5 .5 5 4l4.5-3.5" fill="none" stroke="#2b5fa8"/></svg>Send</span>
      <span><svg width="6" height="9" viewBox="0 0 6 9"><path d="M1 3v4a2 2 0 0 0 4 0V2a1.3 1.3 0 0 0-2.6 0v5" fill="none" stroke="#555"/></svg>Attach</span>
      <span>Discard</span>
    </div>
    <div class="field-btn" style="top:36px">To</div>
    <div class="bcc">Bcc</div>
    <div class="field-rule" style="top:59px"></div>
    <div class="field-btn" style="top:67px">Cc</div>
    <div class="field-rule" style="top:91px"></div>
    <div class="subject">Add a subject</div>
    <div class="body-frame"></div>

    <svg class="wave" width="369" height="77" viewBox="0 0 461 96" aria-hidden="true">
      <path d="M0,62 C120,96 230,70 320,44 S430,22 461,20 L461,96 L0,96Z" fill="var(--gold)"/>
      <path d="M0,36 C40,70 120,84 220,64 C300,46 380,8 461,3 L461,12 C380,18 300,56 222,78 C120,100 40,86 0,58Z" fill="var(--charcoal)"/>
    </svg>

    <div class="brand">
      <span class="mark"></span>
      <div class="name">Northvale</div>
      <div class="tag">BUSINESS SERVICES</div>
    </div>

    <ul class="contact">
      <li>0412555019 <svg width="5" height="5" viewBox="0 0 10 10"><path d="M2 1h2l1 2-1.3 1a6 6 0 0 0 2.3 2.3L7 5l2 1v2a1 1 0 0 1-1 1A8 8 0 0 1 1 2a1 1 0 0 1 1-1z"/></svg></li>
      <li>www.northvalebusinessservices.com.au <svg width="5" height="5" viewBox="0 0 10 10"><circle cx="5" cy="5" r="4"/></svg></li>
      <li>marla@northvalebusinessservices.com.au <svg width="5" height="5" viewBox="0 0 10 10"><rect x="1" y="2" width="8" height="6"/></svg></li>
      <li>18 Ridgeway Crescent Elmhurst VIC 3921 <svg width="5" height="5" viewBox="0 0 10 10"><path d="M5 0a3.5 3.5 0 0 1 3.5 3.5C8.5 6 5 10 5 10S1.5 6 1.5 3.5A3.5 3.5 0 0 1 5 0z"/></svg></li>
    </ul>

    <p class="disclaimer">This e-mail and its attachments are confidential and privileged. Any unauthorised use is expressly prohibited. If you receive this e-mail in error please contact us, then delete the e-mail.</p>

    <div class="eco">
      <svg width="14" height="12" viewBox="0 0 14 12" aria-hidden="true"><rect x="1" y="6" width="10" height="5" fill="var(--leaf)"/><path d="M6 6C6 2 9 1 12 1c0 3-2 5-6 5z" fill="var(--leaf)"/></svg>
      <span>Please consider the environment before printing this e-mail notice.</span>
    </div>
  </section>

</div>
</body>
</html>
```